Poster

I need a poster for my business, www.coastalsupperroutesnerja.example which some information about the most important activities (Sangria Tasting, Iberian Ham, Charcuteries & Sherry Wine Tasting, Sailboat Experiences and Picnic Experiences). A3 Format. Social media included (@coastalsupperroutescsr), contact information included.

```html
<!DOCTYPE html>
<html lang="en">
<head>
<meta charset="utf-8">
<title>Coastal Supper Routes Nerja — Poster</title>
<link href="https://fonts.googleapis.com/css2?family=Bebas+Neue&family=Oswald:wght@200;300;600&family=Montserrat:wght@400;500&display=swap" rel="stylesheet">
<style>
  :root {
    --orange: #f0a323;
    --charcoal: #4a4646;
    --paper: #ffffff;
    --paper-tint: #f7f6f5;
    --ink: #3d3a3a;
  }
  * { margin: 0; padding: 0; box-sizing: border-box; }
  html, body { width: 900px; height: 1200px; overflow: hidden; background: var(--orange); }
  .poster {
    position: relative;
    width: 900px;
    height: 1200px;
    background: var(--orange);
  }
  .poster__sheet {
    position: absolute;
    left: 42px; top: 40px;
    width: 815px; height: 1120px;
    background: var(--paper-tint);
  }
  .brand {
    position: absolute;
    left: 0; width: 900px; top: 86px;
    text-align: center;
    font-family: "Oswald", sans-serif;
    font-weight: 600;
    color: var(--ink);
    font-size: 46px;
    line-height: 1.1;
    text-transform: uppercase;
    letter-spacing: 0.5px;
  }
  .band {
    position: absolute;
    background: var(--charcoal);
    font-family: "Bebas Neue", sans-serif;
    font-size: 80px;
    line-height: 1;
    display: flex;
    align-items: center;
  }
  .band--white { color: var(--paper); }
  .band--orange { color: var(--orange); }
  .band--sangria { left: 42px; top: 246px; width: 546px; height: 103px; padding-left: 66px; }
  .band--iberian { left: 115px; top: 365px; width: 742px; height: 276px; padding-left: 54px; font-size: 78px; line-height: 82px; }
  .band--sailboat { left: 42px; top: 658px; width: 692px; height: 102px; padding-left: 66px; }
  .band--picnic { left: 234px; top: 777px; width: 623px; height: 103px; padding-left: 53px; }
  .phone {
    position: absolute;
    left: 0; width: 900px; top: 905px;
    text-align: center;
    font-family: "Oswald", sans-serif;
    font-weight: 200;
    font-size: 104px;
    line-height: 1.2;
    color: var(--ink);
    letter-spacing: 2px;
  }
  .web {
    position: absolute;
    left: 93px; top: 1032px;
    width: 713px; height: 60px;
    background: var(--charcoal);
    display: flex; align-items: center; justify-content: center;
    font-family: "Oswald", sans-serif;
    font-weight: 300;
    font-size: 27px;
    letter-spacing: 4px;
    color: var(--paper);
  }
  .web__domain { color: var(--orange); }
  .social {
    position: absolute;
    left: 0; width: 900px; top: 1110px;
    display: flex; align-items: center; justify-content: center; gap: 12px;
    font-family: "Montserrat", sans-serif;
    font-size: 22px;
    color: var(--ink);
  }
  .social__dot {
    width: 30px; height: 30px; border-radius: 50%;
    background: var(--orange);
  }
</style>
</head>
<body>
  <main class="poster">
    <div class="poster__sheet" role="img" aria-label="Faint background pattern of hand-drawn food and drink doodles"></div>

    <div class="brand">Coastal Supper Routes<br>Nerja</div>

    <div class="band band--white band--sangria">Sangria Tasting</div>
    <div class="band band--orange band--iberian">Iberian Ham,<br>Charcuteries &amp; Sherry<br>Wine Tasting</div>
    <div class="band band--white band--sailboat">Sailboat Experiences</div>
    <div class="band band--orange band--picnic">Picnic Experiences</div>

    <div class="phone">+34 600 41 27 83</div>

    <div class="web">WWW.<span class="web__domain">COASTALSUPPERROUTESNERJA</span>.EXAMPLE</div>

    <div class="social"><span class="social__dot"></span>@coastalsupperroutescsr</div>
  </main>
</body>
</html>
```